Wandering Rooms Stationary Set

Wandering Rooms is a bespoke interior design firm set to provide services to VIP clients with elegance and minimalism is the main theme for our stationary set. We require a full stationary set covering A4 letterhead, A4 & A3 envelopes, business cards, USB's, CDs, email signature and any other item the designer sees fit. logo is already designed and finalized, and we require the designer to use it as is without modifying the logo.

Address to be used on letterhead / business cards ...etc shall be as follows:

Phone : +971 2 518 2047
P.O. Box : 309186
Address: Block C&D, Bldg. 47, Court 12, Abu Dhabi, United Arab Emirates
Website: www.wanderingrooms-example.com

Target Market(s)

VIP Clients

Industry/Entity Type

Interior Design

Font styles to use
Other font styles liked:
• something to be unique

Colors

Designer to choose colors to be used in the design.

Requirements
Must have
• Elegant, minimalistic
Nice to have
• Simple yet elegant design having a sharp yet clean cut format
Should not have
• No additional colours, just colours that are used in the logo (silver, black or gold)

```html
<!DOCTYPE html>
<html lang="en">
<head>
<meta charset="utf-8">
<title>Wandering Rooms Stationery Set</title>
<link rel="stylesheet" href="https://fonts.googleapis.com/css2?family=Open+Sans:wght@300;400&family=Roboto:wght@400&display=swap">
<style>
  :root {
    --backdrop: #5b5a66;
    --paper: #f4f4f5;
    --paper-shade: #e9e9ec;
    --gold: #c4a56f;
    --gold-flap: #c9aa73;
    --gold-faint: rgba(196, 165, 111, 0.2);
    --ink: #55565c;
    --ink-soft: #6a6b72;
  }
  * { margin: 0; padding: 0; box-sizing: border-box; }
  html, body { width: 1200px; height: 1050px; overflow: hidden; }
  body {
    background: linear-gradient(160deg, #676673 0%, var(--backdrop) 55%, #4b4a55 100%);
    position: relative;
    font-family: "Open Sans", sans-serif;
    color: var(--ink);
  }
  .brand-name {
    font-family: "Open Sans", sans-serif;
    font-weight: 300;
    color: var(--gold);
    white-space: nowrap;
    letter-spacing: 0.02em;
  }
  .contact-list { list-style: none; font-family: "Roboto", sans-serif; color: var(--ink-soft); }
  .contact-list li { display: flex; align-items: center; white-space: nowrap; }
  .contact-list .icon { display: inline-block; border-radius: 50%; background: var(--gold); flex: none; }

  /* Envelope, front with open flap */
  .envelope-front { position: absolute; left: 209px; top: 247px; width: 408px; height: 284px; }
  .envelope-front .flap { position: absolute; left: 0; top: 0; }
  .envelope-front .face {
    position: absolute; left: 0; top: 84px; width: 408px; height: 200px;
    background: linear-gradient(180deg, #f0f0f2, var(--paper));
    box-shadow: 0 6px 10px rgba(0,0,0,0.25);
    overflow: hidden;
  }
  .envelope-front .brand-name { position: absolute; left: 30px; top: 26px; font-size: 19px; }
  .envelope-front .contact-list { position: absolute; left: 30px; top: 148px; font-size: 5.4px; line-height: 7px; }
  .envelope-front .contact-list .icon { width: 4.5px; height: 4.5px; margin-right: 2px; }
  .envelope-front .faint-name {
    position: absolute; left: 342px; top: 98px;
    font-size: 24px; color: var(--gold-faint);
    transform: translate(-50%, -50%) rotate(-90deg);
  }

  /* Envelope, back with closed flap */
  .envelope-back {
    position: absolute; left: 208px; top: 566px; width: 406px; height: 204px;
    background: var(--paper);
    box-shadow: 0 6px 10px rgba(0,0,0,0.25);
  }
  .envelope-back .flap { position: absolute; left: 0; top: 0; }
  .envelope-back .flap-name { position: absolute; left: 0; width: 406px; top: 28px; text-align: center; font-size: 17px; }
  .envelope-back .corner-name { position: absolute; right: 22px; top: 150px; font-size: 16px; }
  .envelope-back .contact-list { position: absolute; left: 26px; top: 157px; font-size: 4.5px; line-height: 6.3px; }
  .envelope-back .contact-list .icon { width: 3.8px; height: 3.8px; margin-right: 2px; }

  /* Letterhead */
  .letterhead {
    position: absolute; left: 660px; top: 259px; width: 395px; height: 523px;
    background: var(--paper);
    box-shadow: 0 6px 12px rgba(0,0,0,0.25);
  }
  .letterhead .fold { position: absolute; left: 0; width: 100%; }
  .letterhead .fold-mid { top: 176px; height: 180px; background: linear-gradient(180deg, #f7f7f8, #ececef); }
  .letterhead .fold-low { top: 356px; height: 167px; background: linear-gradient(180deg, #ebebee, #e3e3e7); }
  .letterhead .brand-name { position: absolute; left: 44px; top: 42px; font-size: 18px; }
  .letterhead .header-rule { position: absolute; left: 246px; top: 40px; width: 1px; height: 25px; background: var(--gold); }
  .letterhead .contact-list {
    position: absolute; left: 256px; top: 39px; font-family: "Open Sans", sans-serif; font-size: 7.2px; line-height: 9px;
  }
  .letterhead .contact-list .icon { width: 6px; height: 6px; margin-right: 3px; }
  .letter-text { position: absolute; left: 45px; width: 306px; font-size: 6.7px; line-height: 9.6px; color: var(--ink); }
  .letter-text.paragraph { text-align: justify; letter-spacing: -0.02px; }
  .salutation { top: 127px; }
  .paragraph-1 { top: 146px; }
  .paragraph-2 { top: 204px; }
  .paragraph-3 { top: 262px; }
  .paragraph-4 { top: 320px; }
  .closing { top: 358px; }
  .signature {
    position: absolute; left: 47px; top: 380px; width: 40px; height: 36px;
    background: linear-gradient(135deg, rgba(42,42,46,0.12), rgba(42,42,46,0.04));
  }
  .letter-address {
    position: absolute; left: 0; top: 482px; width: 100%;
    font-size: 7.2px; display: flex; justify-content: center; align-items: center; color: var(--ink-soft);
  }
  .letter-address .icon { width: 6px; height: 6px; border-radius: 50%; background: var(--gold); margin-right: 3px; }
</style>
</head>
<body>

<section class="envelope-front">
  <svg class="flap" width="408" height="86" viewBox="0 0 408 86" aria-hidden="true">
    <path d="M0,86 L28,8 Q31,0 40,0 L368,0 Q377,0 381,8 L408,86 Z" fill="var(--gold-flap)"/>
  </svg>
  <div class="face">
    <span class="brand-name">Wandering Rooms</span>
    <span class="faint-name brand-name">Wandering Rooms</span>
    <ul class="contact-list">
      <li><span class="icon"></span>+971 2 518 2047</li>
      <li><span class="icon"></span>info@wanderingrooms-example.com</li>
      <li><span class="icon"></span>www.wanderingrooms-example.com</li>
      <li><span class="icon"></span>Block C&amp;D, Bldg. 47, Court 12, Abu Dhabi, United Arab Emirates</li>
    </ul>
  </div>
</section>

<section class="envelope-back">
  <svg class="flap" width="406" height="204" viewBox="0 0 406 204" aria-hidden="true">
    <line x1="388" y1="78" x2="406" y2="204" stroke="#dcdce0" stroke-width="0.8"/>
    <path d="M0,0 L406,0 L378,76 Q373,84 363,84 L43,84 Q33,84 29,76 Z" fill="#f8f8f9" stroke="#dedee2" stroke-width="0.8"/>
  </svg>
  <span class="flap-name brand-name">Wandering Rooms</span>
  <ul class="contact-list">
    <li><span class="icon"></span>+971 2 518 2047</li>
    <li><span class="icon"></span>info@wanderingrooms-example.com</li>
    <li><span class="icon"></span>www.wanderingrooms-example.com</li>
    <li><span class="icon"></span>Block C&amp;D, Bldg. 47, Court 12, Abu Dhabi, United Arab Emirates</li>
  </ul>
  <span class="corner-name brand-name">Wandering Rooms</span>
</section>

<article class="letterhead">
  <div class="fold fold-mid"></div>
  <div class="fold fold-low"></div>
  <span class="brand-name">Wandering Rooms</span>
  <div class="header-rule"></div>
  <ul class="contact-list">
    <li><span class="icon"></span>+971 2 518 2047</li>
    <li><span class="icon"></span>info@wanderingrooms-example.com</li>
    <li><span class="icon"></span>www.wanderingrooms-example.com</li>
  </ul>
  <p class="letter-text salutation">Dear customer,</p>
  <p class="letter-text paragraph paragraph-1">Lorem ipsum dolor sit amet, consectetur adipisicing elit, sed do eiusmod tempor incididunt ut labore et dolore magna aliqua. Ut enim ad minim veniam, quis nostrud exercitation ullamco laboris nisi ut aliquip ex ea commodo consequat. Duis aute irure dolor in reprehenderit in voluptate velit esse cillum dolore eu fugiat nulla pariatur. Excepteur sint occaecat cupidatat non proident, sunt in culpa qui officia deserunt mollit anim id est laborum.</p>
  <p class="letter-text paragraph paragraph-2">Lorem ipsum dolor sit amet, consectetur adipisicing elit, sed do eiusmod tempor incididunt ut labore et dolore magna aliqua. Ut enim ad minim veniam, quis nostrud exercitation ullamco laboris nisi ut aliquip ex ea commodo consequat. Duis aute irure dolor in reprehenderit in voluptate velit esse cillum dolore eu fugiat nulla pariatur. Excepteur sint occaecat cupidatat non proident, sunt in culpa qui officia deserunt mollit anim id est laborum.</p>
  <p class="letter-text paragraph paragraph-3">Lorem ipsum dolor sit amet, consectetur adipisicing elit, sed do eiusmod tempor incididunt ut labore et dolore magna aliqua. Ut enim ad minim veniam, quis nostrud exercitation ullamco laboris nisi ut aliquip ex ea commodo consequat. Duis aute irure dolor in reprehenderit in voluptate velit esse cillum dolore eu fugiat nulla pariatur. Excepteur sint occaecat cupidatat non proident, sunt in culpa qui officia deserunt mollit anim id est laborum.</p>
  <p class="letter-text paragraph paragraph-4">Lorem ipsum dolor sit amet, consectetur adipisicing elit, sed do eiusmod tempor incididunt ut labore et dolore magna aliqua. Ut enim ad minim veniam, quis nostrud exercitation ullamco laboris nisi ut aliquip ex ea commodo consequat. Duis aute irure dolor in reprehenderit.</p>
  <p class="letter-text closing">Yours Sincerely,</p>
  <div class="signature" role="img" aria-label="Handwritten signature of the sender"></div>
  <p class="letter-address"><span class="icon"></span>Block C&amp;D, Bldg. 47, Court 12, Abu Dhabi, United Arab Emirates</p>
</article>

</body>
</html>
```